Counseling Practice Business Card

I need a professional looking business card incorporating my new logo that was just completed. Card needs to incorporate my name and title, description of my specialty, my address, my phone number, my fax number, my email and my website URL. I need to be able to choose design on/with different paper colors and textures.
I do not have a lot of business card ideas so I am open to anything but I want bold,sharp, clear card without additional designs other than my logo (see attached file info). I am open to different color backgrounds or paper colors including black. I do not like traditional brackets around area codes in phone number or dashes between numbers in phone number. Am open to other ways of presenting including periods between numbers as appropriate. I do not know enough to know what I like yet but I want card to coordinate and work together with my logo. My practice emphasizes natural mental health interventions so any use of color (with background paper color or the blue and green in my logo) that elicits nature is nice. In addition to black, any natural brown or wood looking background might be desirable also. Most of the offerings so far look very similar and boring.

Target Market(s)

Potential therapy clients and other professionals

Contact Information for Business Card

Card information:
Gerald M. Whitcombe, Ph.D.
Licensed Clinical Psychologist
Integrative Health Coach
4812 Marlowe Ridge Blvd SE
Suite 310
Duluth, GA 30096
(770) 415-2983 phone
(770) 581-4096 fax
drgeraldwhitcombe@quillmarsh.net
brightfernwellness.net

Font styles to use
Serif
Sans Serif
Other font styles liked:
• anything that you think looks crisp, clear and easily readable

Requirements
Must have
• Any color used should coordinate with my logo design (see attached files).
• Card should be printed horizontally so top and bottom are longest sides of rectangle.
• Background color or paper color should complement and highlight logo. Do not like a white background. black, grey, brown or any color my logo would blend well with.
Nice to have
• I would like designer to utilize color to highlight letters/name or phone-fax-web symbols.
• Bottom edge of card could be highlighted if appropriate to an idea.
Should not have
• I would NOT want the card to have a pure white background at all.
• No clear cards.
• Cards should be oriented with long sides on bottom and top, NOT sides. DO NOT LIKE THIS THIN TALL ORIENTATION.

```html
<!DOCTYPE html>
<html lang="en">
<head>
<meta charset="utf-8">
<title>Brightfern Wellness – Business Card</title>
<link rel="stylesheet" href="https://fonts.googleapis.com/css2?family=Roboto+Condensed:wght@700&family=Source+Sans+3:wght@400;600&display=swap">
<style>
  :root {
    --backdrop: #2b2b2b;
    --card-black: #151515;
    --brand-blue: #2777bf;
    --brand-green: #0b6b39;
    --ink-light: #ffffff;
  }
  * { margin: 0; padding: 0; box-sizing: border-box; }
  html, body {
    width: 1200px; height: 960px; overflow: hidden;
    background: var(--backdrop);
  }
  .stage { position: relative; width: 1200px; height: 960px; }
  .card {
    position: absolute; left: 302px; width: 598px; height: 343px;
    background: var(--card-black);
    box-shadow: 0 4px 14px rgba(0,0,0,.6);
    overflow: hidden;
    font-family: "Source Sans 3", "Myriad Pro", Arial, sans-serif;
  }
  .card--front { top: 122px; }
  .card--back { top: 496px; }
  .card__sweep { position: absolute; inset: 0; }
  .brand-name {
    position: absolute;
    color: var(--brand-blue);
    font-family: "Source Sans 3", Arial, sans-serif;
    font-weight: 600;
    white-space: nowrap;
  }
  .card--front .brand-name { left: 34px; top: 58px; font-size: 33px; }
  .card--back .brand-name { left: 0; right: 0; top: 142px; text-align: center; font-size: 46px; }
  .holder { position: absolute; left: 53px; top: 156px; }
  .holder__name {
    font-family: "Roboto Condensed", "Arial Narrow", sans-serif;
    font-weight: 700; font-size: 19px; color: var(--brand-blue);
    letter-spacing: .2px;
  }
  .holder__role { color: var(--brand-green); font-size: 15.5px; line-height: 20px; }
  .contact {
    position: absolute; right: 25px; top: 198px;
    color: var(--ink-light); text-align: right; font-size: 15px;
  }
  .contact__address { line-height: 20px; margin-bottom: 8px; }
  .contact__line {
    display: flex; justify-content: flex-end; align-items: center;
    gap: 7px; height: 19.5px;
  }
  .contact__icon { width: 13px; height: 13px; flex: none; }
</style>
</head>
<body>
<main class="stage">
  <section class="card card--front" aria-label="Card front">
    <svg class="card__sweep" viewBox="0 0 598 343" width="598" height="343" aria-hidden="true">
      <path fill="var(--brand-green)" d="M95,343 C300,255 515,130 478,0 L486,0 C506,140 330,250 155,343 Z"/>
      <path fill="var(--brand-blue)" d="M155,343 C330,250 506,140 486,0 L598,0 L598,343 Z"/>
    </svg>
    <div class="brand-name">Brightfern Wellness</div>
    <div class="holder">
      <div class="holder__name">GERALD M. WHITCOMBE, PH.D.</div>
      <div class="holder__role">Licensed Clinical Psychologist</div>
      <div class="holder__role">Integrative Health Coach</div>
    </div>
    <div class="contact">
      <div class="contact__address">4812 Marlowe Ridge Blvd SE<br>Suite 310, Duluth, GA 30096</div>
      <div class="contact__line">770.415.2983
        <svg class="contact__icon" viewBox="0 0 14 14" aria-label="Phone"><path fill="#fff" d="M1 4c0-2 2-3 6-3s6 1 6 3v1h-3V4H4v1H1zM3 6h8l2 6H1z"/><circle cx="7" cy="9" r="1.6" fill="var(--brand-blue)"/></svg>
      </div>
      <div class="contact__line">770.581.4096
        <svg class="contact__icon" viewBox="0 0 14 14" aria-label="Fax"><path fill="#fff" d="M3 1h8v4H3zM1 6h12v7H1z"/><rect x="3" y="8" width="8" height="1.5" fill="var(--brand-blue)"/></svg>
      </div>
      <div class="contact__line">drgeraldwhitcombe@quillmarsh.net
        <svg class="contact__icon" viewBox="0 0 14 14" aria-label="Email"><rect x="1" y="3" width="12" height="8" fill="#fff"/><path d="M1 3l6 5 6-5" fill="none" stroke="var(--brand-blue)" stroke-width="1.2"/></svg>
      </div>
      <div class="contact__line">www.brightfernwellness.net
        <svg class="contact__icon" viewBox="0 0 14 14" aria-label="Website"><circle cx="7" cy="7" r="6" fill="#fff"/><path d="M4 4c2 0 2 2 4 2s1 3-1 3M9 10l2-1" fill="none" stroke="var(--brand-blue)" stroke-width="1.3"/></svg>
      </div>
    </div>
  </section>

  <section class="card card--back" aria-label="Card back">
    <div class="brand-name">Brightfern Wellness</div>
  </section>
</main>
</body>
</html>
```